New Company Business Card design

Looking for a corporate looking business card utilising my new logo design - the logo i would like embossed as one option and flat as another - simplistic but stylish - less is more - we are an import export business launching into the market - i would like a couple of options as main background - Grey or Black

```html
<!DOCTYPE html>
<html lang="en">
<head>
<meta charset="utf-8">
<title>Meridian Trade Partners – Business Card</title>
<link href="https://fonts.googleapis.com/css2?family=Roboto:wght@400;500&display=swap" rel="stylesheet">
<style>
  :root {
    --backdrop: #3a3b3e;
    --card-front: #ffffff;
    --card-front-shade: #eceef0;
    --card-back: #5c5d61;
    --card-back-shade: #4e4f53;
    --brand-blue: #1f72bf;
    --ink: #3b3d40;
    --ink-soft: #55585c;
    --back-text: #c9cacc;
  }
  * { box-sizing: border-box; margin: 0; padding: 0; }
  html, body { width: 1200px; height: 900px; overflow: hidden; }
  body {
    background: var(--backdrop);
    font-family: "Roboto", Arial, sans-serif;
    display: flex;
    flex-direction: column;
    align-items: center;
    justify-content: center;
    gap: 60px;
  }
  .card {
    width: 560px;
    height: 320px;
    border-radius: 22px;
    position: relative;
    overflow: hidden;
  }
  .card-front {
    background: linear-gradient(160deg, var(--card-front) 55%, var(--card-front-shade));
  }
  .card-back {
    background: linear-gradient(160deg, var(--card-back) 40%, var(--card-back-shade));
    display: flex;
    align-items: center;
    justify-content: center;
  }
  .brand {
    display: flex;
    align-items: center;
    gap: 10px;
    color: var(--brand-blue);
    font-weight: 500;
    font-size: 20px;
    letter-spacing: 0.08em;
    text-transform: uppercase;
  }
  .brand-dot {
    width: 14px; height: 14px; border-radius: 50%;
    background: currentColor;
  }
  .card-front .brand { position: absolute; left: 44px; top: 52px; }
  .card-back .brand { color: var(--back-text); font-size: 26px; }
  .divider {
    position: absolute;
    left: 44px; right: 44px; top: 168px;
    height: 2px;
    background: var(--brand-blue);
  }
  .holder {
    position: absolute;
    right: 44px; top: 112px;
    text-align: right;
  }
  .holder-name {
    color: var(--brand-blue);
    font-size: 24px;
    font-weight: 500;
    letter-spacing: 0.04em;
    text-transform: uppercase;
  }
  .holder-title { color: var(--ink-soft); font-size: 15px; margin-top: 2px; }
  .contact-list {
    position: absolute;
    left: 44px; top: 196px;
    list-style: none;
    color: var(--ink);
    font-size: 15px;
    line-height: 26px;
  }
  .contact-list li { display: flex; align-items: center; gap: 10px; }
  .contact-list svg { width: 12px; height: 12px; fill: var(--brand-blue); flex: none; }
  .address {
    position: absolute;
    right: 44px; top: 196px;
    text-align: right;
    color: var(--ink);
    font-size: 15px;
    line-height: 24px;
  }
</style>
</head>
<body>
  <section class="card card-front">
    <div class="brand"><span class="brand-dot"></span>Meridian Trade Partners</div>
    <div class="holder">
      <p class="holder-name">Daniel Price</p>
      <p class="holder-title">Director</p>
    </div>
    <div class="divider"></div>
    <ul class="contact-list">
      <li><svg viewBox="0 0 24 24"><path d="M6.6 10.8a15 15 0 0 0 6.6 6.6l2.2-2.2c.3-.3.7-.4 1-.2 1.1.4 2.3.6 3.6.6.6 0 1 .4 1 1V20c0 .6-.4 1-1 1A17 17 0 0 1 3 4c0-.6.4-1 1-1h3.5c.6 0 1 .4 1 1 0 1.3.2 2.5.6 3.6.1.3 0 .7-.2 1z"/></svg>615-555-0142</li>
      <li><svg viewBox="0 0 24 24"><path d="M2 5h20v14H2zm2 2v.5l8 5 8-5V7l-8 5z"/></svg>info@meridiantrade.com</li>
      <li><svg viewBox="0 0 24 24"><circle cx="12" cy="12" r="10"/></svg>www.meridiantrade.com</li>
    </ul>
    <address class="address">2250 Harbor View Rd<br>Linden, CA 95236-0418</address>
  </section>

  <section class="card card-back">
    <div class="brand"><span class="brand-dot"></span>Meridian Trade Partners</div>
  </section>
</body>
</html>
```